we can communicate on this, but i want to follow the approach we took on Pellew|Marsh & Quinlan but i feel the card front needs the black background and the platinum and gold logo. The back? I am open. we can use the same info from PM&Q. Velmont Arc is an enhanced equity investment fund - basically a very exclusive boutique hedge fund that uses only stock options. very advanced things. hope you are interested

Contact Information for Business Card

Dr. Lewis T. Brennick, CFA
Scientifique de fusée financière
701.555.0143
LTBquant47@mailvantor.com

4718 Willow Creek Bend W.
West Fargo, ND 58078

No web site

Colors

Designer to choose colors to be used in the design.

Requirements
Nice to have
• I tend to prefer the most visible applications of the logo to include logo and name, the logo version with a black background and the gold and platinum components separated by the black. I see this working well for a single side (logo and name - this is card front to me).
• I am fairly open to other treatments on the reverse side with the data. To me, it makes sense to have a different color rendition of the logo on the reverse and it may be a muted black tone on tone or an oversized portion that would have spot UV. Or, the reverse may play with colors and layout
Should not have
• Other colors = no no
• Decorative font

```html
<!DOCTYPE html>
<html lang="en">
<head>
<meta charset="utf-8">
<title>Velmont Arc — Business Card</title>
<link rel="stylesheet" href="https://fonts.googleapis.com/css2?family=Roboto:ital,wght@0,400;0,500;0,700;1,400&display=swap">
<style>
  :root {
    --backdrop: #1a1a1b;
    --card: #1f2022;
    --card-edge: #2a2b2d;
    --platinum: #c8c9cc;
    --platinum-dim: #8d8e91;
    --gold: #d2ac37;
    --white: #f2f2f2;
    --tone: #242527;
  }
  * { box-sizing: border-box; margin: 0; padding: 0; }
  html, body {
    width: 1200px; height: 800px; overflow: hidden;
    background: var(--backdrop);
    font-family: "Roboto", Arial, sans-serif;
  }
  .canvas {
    width: 1200px; height: 800px;
    display: flex; flex-direction: column; align-items: center; justify-content: center;
    gap: 40px;
  }
  .card {
    position: relative; overflow: hidden;
    width: 580px; height: 331px;
    background: var(--card);
    border: 1px solid var(--card-edge);
    box-shadow: 0 10px 30px rgba(0,0,0,.45);
  }

  /* Front */
  .card-front {
    display: flex; flex-direction: column; align-items: center; justify-content: center;
  }
  .front-mark {
    width: 92px; height: 92px; border-radius: 50%;
    background: var(--platinum-dim);
    margin-bottom: 22px;
  }
  .front-name {
    color: var(--platinum); font-weight: 700; text-align: center; line-height: 1;
  }
  .front-name .word-main { display: block; font-size: 46px; letter-spacing: 2px; }
  .front-name .word-sub { display: block; font-size: 20px; letter-spacing: 9px; margin-top: 8px; padding-left: 9px; }

  /* Back */
  .tone-circle {
    position: absolute; left: 300px; top: 10px;
    width: 300px; height: 300px; border-radius: 50%;
    background: var(--tone);
  }
  .brand {
    position: absolute; left: 48px; top: 34px;
  }
  .brand-mark {
    width: 64px; height: 64px; border-radius: 50%;
    background: var(--gold);
    margin: 0 0 12px 34px;
  }
  .brand-name { color: var(--white); font-weight: 700; line-height: 1; }
  .brand-name .word-main { display: block; font-size: 32px; letter-spacing: 1px; }
  .brand-name .word-sub { display: block; font-size: 15px; letter-spacing: 7px; margin-top: 5px; padding-left: 36px; }

  .address {
    position: absolute; left: 48px; top: 212px;
    color: var(--white); font-size: 13px; line-height: 1.35; font-style: normal;
  }
  .contacts {
    position: absolute; left: 48px; top: 262px;
    list-style: none; color: var(--white); font-size: 13px; line-height: 1.45;
  }
  .contacts li { display: flex; align-items: center; gap: 9px; }
  .contacts svg { width: 11px; height: 11px; flex: none; }

  .person {
    position: absolute; right: 38px; top: 210px; text-align: right;
  }
  .person-name { color: var(--gold); font-weight: 700; font-size: 20px; }
  .person-name .credential { font-size: 11px; font-weight: 500; vertical-align: 5px; }
  .person-title { color: var(--white); font-style: italic; font-size: 13px; margin-top: 3px; }
</style>
</head>
<body>
<main class="canvas">

  <section class="card card-front" aria-label="Card front">
    <div class="front-mark"></div>
    <h1 class="front-name">
      <span class="word-main">VELMONT</span>
      <span class="word-sub">ARC</span>
    </h1>
  </section>

  <section class="card card-back" aria-label="Card back">
    <div class="tone-circle"></div>

    <div class="brand">
      <div class="brand-mark"></div>
      <h2 class="brand-name">
        <span class="word-main">VELMONT</span>
        <span class="word-sub">ARC</span>
      </h2>
    </div>

    <address class="address">
      4718 Willow Creek Bend W.<br>
      West Fargo, ND 58078
    </address>

    <ul class="contacts">
      <li>
        <svg viewBox="0 0 12 12" aria-hidden="true"><rect x="3" y="0.5" width="6" height="11" rx="1" fill="none" stroke="var(--gold)" stroke-width="1.3"/><circle cx="6" cy="9.5" r=".7" fill="var(--gold)"/></svg>
        701.555.0143
      </li>
      <li>
        <svg viewBox="0 0 12 12" aria-hidden="true"><rect x="0.5" y="2" width="11" height="8" fill="var(--gold)"/><path d="M0.5 2 L6 6.5 L11.5 2" fill="none" stroke="var(--card)" stroke-width="1"/></svg>
        LTBquant47@mailvantor.com
      </li>
    </ul>

    <div class="person">
      <p class="person-name">Dr. Lewis T. Brennick, <span class="credential">CFA</span></p>
      <p class="person-title">Scientifique des Fusées Financières</p>
    </div>
  </section>

</main>
</body>
</html>
```